Healthy Meal Delivery Website Needs to be updated, current, fresh and modern

Hi there,

The current website i have is super old and outdated.

I would like a beautiful modern site that has all the same content as the previous except with a a new, modern and trustworthy feel.

The current website is https://tovalplatefresh.com/

Target Market(s)

Health Conscious Young Professionals

Industry/Entity Type

Food Service

Font styles to use
Sans Serif

Requirements
Must have
• Modern Trustworthy feel
Should not have
• Anything out dated or cheesy or scammy

```html
<!DOCTYPE html>
<html lang="en">
<head>
<meta charset="utf-8">
<title>Toval Plate – Fresh Diet Meals Delivered</title>
<link href="https://fonts.googleapis.com/css2?family=Montserrat:wght@600;700;800&family=Lato:wght@400;700&display=swap" rel="stylesheet">
<style>
:root{
  --blue:#1e8fd6;
  --blue-dark:#1570b5;
  --blue-light:#47aee8;
  --yellow:#e6e61a;
  --yellow-deep:#d9d800;
  --ink:#2b2b2b;
  --grey:#8a8a8a;
  --light:#f4f4f4;
  --footer:#1c1c1c;
  --white:#ffffff;
}
*{box-sizing:border-box;margin:0;padding:0}
html,body{width:1200px;height:3529px;overflow:hidden;background:var(--white)}
body{position:relative;font-family:"Lato",sans-serif;color:var(--ink)}
.abs{position:absolute}
h1,h2,h3,.heading{font-family:"Montserrat",sans-serif}

/* top bar */
.topbar{left:0;top:0;width:1200px;height:38px;background:linear-gradient(90deg,var(--blue-dark),var(--blue-light));color:var(--white);font-size:12px}
.topbar .contact{left:99px;top:12px;display:flex;gap:28px}
.topbar .like{left:712px;top:8px;display:flex;gap:4px}
.topbar .like span{background:#3b5a9a;color:#fff;font-size:11px;padding:3px 7px;border-radius:2px}
.topbar .login{left:833px;top:0;height:38px;width:140px;background:var(--yellow);color:var(--blue-dark);font-size:12px;font-weight:700;display:flex;align-items:center;justify-content:center}
.topbar .signup{left:973px;top:0;height:38px;width:128px;background:var(--blue-dark);font-size:12px;font-weight:700;display:flex;align-items:center;justify-content:center}

/* nav */
.brand{display:flex;align-items:center;gap:10px;font-family:"Montserrat",sans-serif;font-weight:800;font-size:24px;color:var(--blue)}
.brand i{width:26px;height:26px;border-radius:50%;background:var(--yellow);display:block}
.nav-brand{left:99px;top:70px}
.nav{left:462px;top:82px;display:flex;gap:30px;font-size:12px;font-family:"Montserrat",sans-serif;font-weight:600;color:#555}
.nav .active{color:var(--yellow-deep);border-bottom:2px solid var(--yellow-deep);padding-bottom:4px}

/* hero */
.hero-photo{left:0;top:140px;width:1200px;height:540px}
.hero-card{left:99px;top:165px;width:494px;height:494px;border-radius:50%;background:var(--blue);border:10px solid var(--yellow);color:var(--white);padding:110px 0 0 62px}
.hero-card h1{font-size:27px;line-height:1.35;font-weight:800;letter-spacing:.5px}
.hero-card .mark{width:36px;height:14px;border-radius:7px;background:var(--yellow);margin-bottom:18px}
.hero-card ul{list-style:none;margin-top:20px;font-size:13px;line-height:2.1}
.hero-card li{display:flex;align-items:center;gap:12px}
.tick{width:14px;height:14px;border-radius:50%;background:var(--white);display:inline-flex;align-items:center;justify-content:center}
.dots{left:1026px;top:525px;display:flex;gap:10px}
.dots span{width:26px;height:26px;border-radius:50%;background:var(--blue);color:#fff;font-size:12px;font-weight:700;display:flex;align-items:center;justify-content:center;border:2px solid #fff}

.mark-sm{width:40px;height:14px;border-radius:7px;background:var(--yellow)}
.section-title{width:1200px;text-align:center;font-weight:800;font-size:30px;line-height:1.45;color:var(--ink)}
.section-title em{font-style:normal;color:var(--blue)}
.lead{width:1200px;text-align:center;font-size:14px;line-height:2.3;color:var(--grey)}

/* features */
.feature h3{font-size:14px;font-weight:700;color:var(--blue);margin-bottom:10px}
.feature p{font-size:13px;line-height:1.9;color:var(--grey)}
.feature.left{text-align:right;width:260px}
.feature.right{width:270px}
.bubble{width:114px;height:114px;border-radius:50%}
.bubble.y{background:var(--yellow)}
.bubble.b{background:var(--blue)}

/* about band */
.band{left:0;top:1475px;width:1200px;height:750px}
.band-text{left:99px;top:1550px;width:450px;color:var(--white)}
.band-text h2{font-size:27px;font-weight:800;margin-top:16px}
.band-text .sub{color:var(--yellow);font-size:14px;margin:8px 0 24px}
.band-text h3{font-size:15px;font-weight:700;display:flex;align-items:center;gap:10px;margin-top:18px}
.band-text h3 i{width:18px;height:8px;border-radius:4px;background:var(--white);display:block}
.band-text p{font-size:13px;line-height:1.9;margin-top:8px}
.monitor{left:616px;top:1741px;width:398px;height:287px}
.monitor .screen{position:absolute;left:0;top:0;width:398px;height:245px;background:#222;border-radius:8px;padding:12px}
.monitor .screen div{width:100%;height:100%}
.monitor .stand{position:absolute;left:0;top:245px;width:398px;height:42px;background:linear-gradient(#e4e4e4,#bdbdbd);border-radius:0 0 6px 6px}

/* menu */
.menu-card{width:324px}
.menu-card .img{height:153px;border-radius:6px}
.menu-card .label{margin-top:8px;height:35px;background:var(--yellow);border-radius:3px;color:var(--blue);font-family:"Montserrat",sans-serif;font-weight:700;font-size:13px;display:flex;align-items:center;justify-content:center}
.arrow{font-size:26px;color:#333}

/* testimonial */
.quote-wrap{left:470px;top:2960px;width:630px;color:var(--white);text-align:center}
.quote-wrap h2{font-size:28px;font-weight:800;margin-top:14px}
.quote-wrap .qmark{position:absolute;left:0;top:58px;font-family:Georgia,serif;font-size:48px;font-weight:700}
.quote-wrap p{font-size:13px;line-height:2.6;font-style:italic;margin-top:14px}
.q-dots{left:770px;top:3138px;display:flex;gap:6px}
.q-dots span{width:9px;height:9px;border-radius:50%;border:1.5px solid #fff}
.q-dots span.on{background:#fff}
.q-author{left:1040px;top:3133px;color:#fff;font-size:14px;font-style:italic}

/* footer */
.social{left:296px;top:3345px;display:flex;gap:22px}
.social span{width:48px;height:48px;border-radius:50%;border:2px solid var(--white);display:block}
.foot-nav{left:152px;top:3428px;display:flex;gap:24px;color:var(--white);font-size:12px;font-family:"Montserrat",sans-serif;font-weight:600}
.copy{left:0;top:3468px;width:835px;text-align:center;color:#ddd;font-size:12px}
.copy b{color:var(--yellow);font-weight:400}
.foot-brand{left:870px;top:3403px}
.foot-brand.brand{color:var(--yellow);font-size:22px}
.divider{left:835px;top:3320px;width:1px;height:180px;background:#444}
</style>
</head>
<body>

<header>
  <div class="abs topbar">
    <div class="abs contact"><span>&#9742; Phone: (416) 555-0142</span><span>&#9993; Email: hello@tovalplate.com</span></div>
    <div class="abs like"><span>Like</span><span>Share</span></div>
    <div class="abs login">CUSTOMER LOGIN</div>
    <div class="abs signup">SIGN UP NOW</div>
  </div>
  <div class="abs brand nav-brand"><i></i>Toval Plate</div>
  <nav class="abs nav">
    <span class="active">HOME</span><span>TOVAL MEAL PLANS</span><span>MENU</span><span>PRICING</span><span>ABOUT</span><span>PRESS</span><span>CONTACT</span><span>SIGN UP</span><span>LOGIN</span>
  </nav>
</header>

<section class="hero">
  <div class="abs hero-photo" role="img" aria-label="Fresh ingredients on a table: grains, salmon, eggs, nuts, avocado and vegetables" style="background:linear-gradient(120deg,#cfc6b6 0%,#b58a6c 35%,#9b4a3e 50%,#c9b784 70%,#7d9a4a 100%)"></div>
  <svg class="abs" style="left:0;top:560px" width="1200" height="150" viewBox="0 0 1200 150" aria-hidden="true">
    <path d="M0 150 L0 100 Q600 140 1200 0 L1200 150 Z" fill="#fff"/>
    <path d="M0 100 Q600 140 1200 0 L1200 14 Q600 158 0 118 Z" fill="var(--yellow)"/>
  </svg>
  <div class="abs hero-card">
    <div class="mark"></div>
    <h1>FRESH DIET MEALS<br>DELIVERED</h1>
    <ul>
      <li><span class="tick"><svg width="8" height="8" viewBox="0 0 8 8"><path d="M1 4l2 2 4-5" stroke="#1e8fd6" stroke-width="1.6" fill="none"/></svg></span>Real food you'll love to eat</li>
      <li><span class="tick"><svg width="8" height="8" viewBox="0 0 8 8"><path d="M1 4l2 2 4-5" stroke="#1e8fd6" stroke-width="1.6" fill="none"/></svg></span>Portion controlled meals to maximize your weight loss</li>
      <li><span class="tick"><svg width="8" height="8" viewBox="0 0 8 8"><path d="M1 4l2 2 4-5" stroke="#1e8fd6" stroke-width="1.6" fill="none"/></svg></span>No grocery shopping, cooking or cleaning required</li>
      <li><span class="tick"><svg width="8" height="8" viewBox="0 0 8 8"><path d="M1 4l2 2 4-5" stroke="#1e8fd6" stroke-width="1.6" fill="none"/></svg></span>Freshly prepared by our in house chefs</li>
    </ul>
  </div>
  <div class="abs dots"><span>1</span><span>2</span><span>3</span><span>4</span></div>
</section>

<section class="intro">
  <div class="abs mark-sm" style="left:580px;top:800px"></div>
  <h2 class="abs section-title" style="left:0;top:830px">THE TOVAL DIET <em>DELIVERS</em> DIET MEALS TO YOUR DOOR<br>IN TORONTO, GTA AND MONTREAL</h2>
  <p class="abs lead" style="left:0;top:925px">Our fresh and delicious diet meals and snacks are made with only the best natural ingredients that nourish<br>your body. Why not let us prepare your meals while you lose the weight?</p>
  <div class="abs" style="left:460px;top:1025px;width:280px;height:1px;background:#e6e6e6"></div>

  <div class="abs feature left" style="left:180px;top:1075px"><h3>HEALTHY</h3><p>The Toval Diet is a great way to ensure you are eating all the nutrients you need, and nothing your body doesn't need.</p></div>
  <div class="abs bubble y" style="left:458px;top:1068px" role="img" aria-label="Healthy icon"></div>
  <div class="abs bubble b" style="left:621px;top:1068px" role="img" aria-label="Choice icon"></div>
  <div class="abs feature right" style="left:758px;top:1075px"><h3>CHOICE</h3><p>You can choose your own meals from over 100 tasty entrees, desserts and snack foods. You can choose your.</p></div>

  <div class="abs mark-sm" style="left:580px;top:1200px;width:36px;height:12px;background:var(--blue)"></div>

  <div class="abs feature left" style="left:180px;top:1240px"><h3>FRESH</h3><p>All of our meals are real food, freshly prepared by our in-house expert chefs.</p></div>
  <div class="abs bubble b" style="left:458px;top:1221px" role="img" aria-label="Fresh icon"></div>
  <div class="abs bubble y" style="left:621px;top:1221px" role="img" aria-label="Customized icon"></div>
  <div class="abs feature right" style="left:758px;top:1228px"><h3>CUSTOMIZED</h3><p>Your meals will be delivered fresh to your door, customized for your unique body type and level of activity.</p></div>
</section>

<section class="about">
  <div class="abs band" role="img" aria-label="Blue tinted photo of fresh vegetables" style="background:radial-gradient(circle at 30% 40%,#3ba4e2,#1a7fc6 70%)"></div>
  <svg class="abs" style="left:0;top:1475px" width="1200" height="750" viewBox="0 0 1200 750" aria-hidden="true">
    <path d="M1200 0 Q760 60 690 360 Q660 640 1200 740 Z" fill="var(--yellow)"/>
    <path d="M0 735 Q600 760 1200 700 L1200 750 L0 750 Z" fill="#fff"/>
  </svg>
  <div class="abs band-text">
    <div class="mark-sm"></div>
    <h2>The Toval Diet</h2>
    <p class="sub">Real foods designed by nature prepared by Toval.</p>
    <h3><i></i>WHAT YOU GET</h3>
    <p>Toval Diet Delivery provides you with 3 fresh daily meals and 3 snacks<br>delivered to your doorstep before 6am.</p>
    <h3><i></i>SELECTION</h3>
    <p>Choose your meals from over 100 delicious entrees, snacks and desserts.</p>
    <h3><i></i>LUXURY</h3>
    <p>Enjoy the luxury of having your own personal chef and nutritionist prepare<br>Toval Diet meals for you.</p>
    <h3><i></i>WHAT IS PHASE 1?</h3>
    <p>Phase 1 is the stricter phase that eliminates bad carbs and processed foods;<br>no sugar, candy, pasta or bread.</p>
    <h3><i></i>WHAT IS PHASE 1?</h3>
    <p>Phase 1 is the stricter phase that eliminates bad carbs and processed foods;<br>no sugar, candy, pasta or bread.</p>
  </div>
  <div class="abs monitor">
    <div class="screen"><div role="img" aria-label="Grilled salmon fillet with lime" style="background:linear-gradient(135deg,#7a3b22,#d9743f 50%,#5d2a18)"></div></div>
    <div class="stand"></div>
  </div>
  <div class="abs" role="img" aria-label="Smiling woman in a green sweater and jeans" style="left:1035px;top:1859px;width:141px;height:365px;border-radius:60px 60px 10px 10px;background:linear-gradient(#c79a5a 0%,#6fae97 35%,#3f6f9a 100%)"></div>
  <div class="abs" style="left:900px;top:2115px;width:44px;height:22px;border-radius:11px;background:var(--blue)"></div>
</section>

<section class="menu">
  <div class="abs mark-sm" style="left:580px;top:2338px"></div>
  <h2 class="abs section-title" style="left:0;top:2370px">SELECT FROM <em>OVER 100</em> MENU ITEMS</h2>
  <p class="abs lead" style="left:0;top:2425px">You can choose your own meals from over 100 tasty entrees, desserts and snack foods. You can choose<br>your meals online, or we can select your meals for you.</p>
  <div class="abs arrow" style="left:60px;top:2596px">&#8249;</div>
  <div class="abs arrow" style="left:1126px;top:2596px">&#8250;</div>
  <div class="abs menu-card" style="left:99px;top:2522px"><div class="img" role="img" aria-label="Lunch salad with chicken and greens" style="background:linear-gradient(135deg,#8fae6a,#d8d2c0,#6b8a45)"></div><div class="label">LUNCH</div></div>
  <div class="abs menu-card" style="left:440px;top:2522px"><div class="img" role="img" aria-label="Breakfast frittata" style="background:linear-gradient(135deg,#7a5a3a,#e2b96a,#5a4030)"></div><div class="label">BREAKFAST</div></div>
  <div class="abs menu-card" style="left:779px;top:2522px"><div class="img" role="img" aria-label="Fresh fruit cup snack" style="background:linear-gradient(135deg,#d8d8d8,#b8283a,#e7e2dc)"></div><div class="label">MIDAFTERNOON</div></div>
</section>

<section class="testimonial">
  <svg class="abs" style="left:0;top:2820px" width="1200" height="520" viewBox="0 0 1200 520" aria-hidden="true">
    <defs><linearGradient id="tg" x1="0" y1="0" x2="1" y2="1"><stop offset="0" stop-color="#2a9ae0"/><stop offset="1" stop-color="#1672b8"/></linearGradient></defs>
    <path d="M0 25 L1200 0 L1200 520 L0 520 Z" fill="url(#tg)"/>
    <path d="M0 25 L1200 0 L1200 10 L0 35 Z" fill="var(--yellow)"/>
  </svg>
  <div class="abs" style="left:35px;top:2970px;width:300px;height:140px;border-radius:150px 10px 150px 10px;background:#4fb38a;opacity:.85"></div>
  <div class="abs" role="img" aria-label="Portrait of a smiling customer holding a salad" style="left:150px;top:3000px;width:274px;height:259px;border-radius:200px 20px 200px 20px;border:4px solid #fff;background:linear-gradient(135deg,#e7d2c0,#b88a6a 50%,#f0e6dc)"></div>
  <div class="abs quote-wrap">
    <div class="mark-sm" style="margin:0 auto"></div>
    <h2>WHAT THEY SAY</h2>
    <span class="qmark">&ldquo;</span>
    <p>Ok, so you know I loved Toval food the first time but somehow, the second time I love it even more.<br>My lentil soup was incredible! And I am loooving these huge snacks - melba, cheese, veggies,<br>turkey pepperoni - I feel like I am able to graze all day long! So brilliant!"</p>
  </div>
  <div class="abs q-dots"><span class="on"></span><span></span><span></span></div>
  <div class="abs q-author">- Marisa</div>
</section>

<footer>
  <svg class="abs" style="left:0;top:3230px" width="1200" height="299" viewBox="0 0 1200 299" aria-hidden="true">
    <path d="M0 60 Q600 10 1200 90 L1200 299 L0 299 Z" fill="var(--footer)"/>
    <path d="M0 60 Q600 10 1200 90 L1200 78 Q600 -4 0 48 Z" fill="var(--yellow)"/>
  </svg>
  <div class="abs social"><span></span><span></span><span></span><span></span></div>
  <nav class="abs foot-nav"><span>HOME</span><span>TOVAL MEAL PLANS</span><span>MENU</span><span>PRICING</span><span>ABOUT</span><span>PRESS</span><span>CONTACT</span><span>SIGN UP</span><span>LOGIN</span></nav>
  <p class="abs copy">&copy; Copyright 2018 <b>Toval Plate</b>.All Rights Reserved &nbsp;|&nbsp; Privacy policy</p>
  <div class="abs divider"></div>
  <div class="abs brand foot-brand"><i></i>Toval Plate</div>
</footer>

</body>
</html>
```